Flyer, poster, banner and social media titles designs for Community Mending Chartre

The Harbourline Charter for Community Mending provide a nationally agreed framework to guide recovery policy and practice across Australia. The Principles support recovery practitioners, governments, non-government organisations and communities to deliver effective, community-centred recovery outcomes.
The Principles have recently been refreshed through extensive consultation and we require a contemporary visual identity and design suite that will increase awareness, engagement and practical application of the Principles.
The redesign will cover:
• A4 Brochure (primary publication)
• A3 Poster
• Pull up banner
• Social Media Tiles
The new design should:
• Create a recognisable brand for the Harbourline Charter.
• Appeal to both experienced and emerging recovery practitioners.
• Reflect contemporary disaster recovery practice.
• Feel people-focused rather than government-focused.
• Support future resources such as videos, implementation guides, presentations and workshop materials.
• Remain relevant for several years without requiring a major redesign.
Target Audience
• Disaster recovery practitioners
• Government agencies
• Non-government organisations
• Community recovery workers
• Recovery managers and leaders
• Community stakeholders and volunteers
The visual identity should reflect the six Principles:
• Understanding Context
• Recognising Complexity
• Community-Centred Approaches
• Coordination
• Communication
• Capacity Building
The design should communicate:
• Recovery is centred on people and communities.
• Recovery is collaborative and involves many sectors.
• Recovery is adaptive, inclusive and evidence-informed.
• Recovery supports resilience and long-term wellbeing.
• The Principles provide practical guidance for recovery practice.
We are looking for:
• Modern and professional
• Warm and approachable
• Human-centred
• Inclusive and accessible
• Australian in context
• Visually engaging
• Suitable for print and digital use
We would like to avoid:
• Images of disaster destruction
• Emergency response imagery (fire trucks, flashing lights, etc.)
• Overly corporate or bureaucratic designs
• Designs that focus on deficits rather than recovery and growth
Consider themes such as:
• Connection and collaboration
• Communities and people
• Growth, recovery and renewal
Accessibility
Designs should:
• Meet accessibility best practice
• Use clear typography
• Achieve strong colour contrast
• Be suitable for both digital and print formats

Deliverables
1. Principles Brochure
• A4 trifold size x 2 (online and print friendly version)
• A side to include cover side, logos side and overview of principles.
• B side full details of the principles
• Graphic to highlight the 3 c’s concept (RECOVERY Context, complexity, community centred, coordinate, communicate and capacity). Currently 3 circles.
• Can be printed and distributed electronically
2. Poster
• A1 and A3 versions
• Suitable for office and workshop display
3. Pull-Up Banner - 850 mm (W) × 2000 mm (H)
• Conference and event use
• High visual impact
• Strong branding and concise messaging
4. Social Media Tiles x 3

We are providing an extension and increasing the budget following feedback from designers. We are wanting the resources to look and feel different from the existing designs, considering either a different colour palette in the designs or different motif with the leave design. Any nature based designs should consider the Australian fauna or flora. Also suggest avoiding images in the designs. The principles are not numbered or liner in the concept of how they function. Happy to answer any further questions and thank you for your suggested concepts.

Disaster recovery practitioners, Government agencies , Non-government organisations, Community recovery workers and Community stakeholders and volunteers

Disaster recovery

• Modern, warm, visually engaging, human-centred, Australian in context and different to the current design.
• Symbols for each principles
• Images of disaster destruction, Emergency response imagery, Overly corporate or bureaucratic designs, Designs that focus on deficits rather than recovery and growth, avoid too much black

```html
<!DOCTYPE html>
<html lang="en">
<head>
<meta charset="utf-8">
<title>Harbourline Charter for Community Mending – Trifold Brochure</title>
<link rel="stylesheet" href="https://fonts.googleapis.com/css2?family=Inter:wght@300;400;500&family=Lexend:wght@400;500;600&display=swap">
<style>
  :root{
    --backdrop:#8fadd6;
    --paper:#f2e9e0;
    --paper-mid:#e8dfd5;
    --sage:#d3dbc7;
    --sage-box:#d2dac6;
    --white:#ffffff;
    --green:#3f7b2b;
    --ink:#262626;
    --body:#3a3a3a;
    --rule:#9fb890;
    --logo-grey:#b9b2a8;
  }
  *{box-sizing:border-box;margin:0;padding:0}
  html,body{width:864px;height:1200px;overflow:hidden;background:var(--backdrop)}
  body{position:relative;font-family:"Inter",sans-serif;font-weight:300;color:var(--body)}

  .sheet{position:absolute;left:57px;width:750px;height:531px;display:flex;box-shadow:0 14px 18px -10px rgba(40,60,90,.45)}
  .sheet--outer{top:54px}
  .sheet--inner{top:615px}
  .panel{width:250px;height:100%;overflow:hidden;position:relative}

  h2,h3,h4{font-family:"Lexend",sans-serif;color:var(--ink);font-weight:500}
  .accent{color:var(--green)}
  p{font-size:8.6px;line-height:11.7px;letter-spacing:-.15px}

  /* Outer sheet */
  .panel--intro{background:var(--paper);padding:18px 14px 0 16px}
  .intro-title{font-size:15.5px;line-height:19px;color:var(--green);font-weight:600;letter-spacing:-.3px;margin-bottom:10px;white-space:nowrap}
  .panel--intro p{margin-bottom:5px}
  .relationship{margin:10px -6px 0 -8px;background:var(--sage-box);border-radius:4px;padding:9px 10px}
  .relationship h4{font-family:"Inter",sans-serif;font-weight:400;font-size:10px;margin-bottom:5px}
  .relationship p{margin-bottom:0}
  .success-label{font-family:"Lexend",sans-serif;font-weight:500;color:var(--green);font-size:11.5px;margin:13px 0 5px;letter-spacing:-.1px}
  .principle-sm{font-family:"Inter",sans-serif;font-weight:500;font-size:10px;margin:9px 0 4px}
  .principle-sm:first-of-type{margin-top:0}

  .panel--overview{background:linear-gradient(90deg,var(--paper-mid),var(--paper) 55%,#e6ddd2);padding:14px 12px 0 13px}
  .panel--overview .principle-sm{margin-top:8px}
  .partner-box{position:absolute;left:22px;top:326px;width:205px;height:183px;background:#f6f0ea;border:1px solid #d8cfc4;border-radius:6px;box-shadow:0 1px 3px rgba(0,0,0,.15)}
  .partner-box svg{display:block}

  .panel--cover{background:var(--paper);text-align:center}
  .brand{position:absolute;left:48px;top:46px;display:flex;align-items:center;gap:8px;text-align:left}
  .brand-mark{width:34px;height:34px;border-radius:50%;border:3px solid #3aa6d6}
  .brand-name{font-family:"Lexend",sans-serif;font-weight:400;font-size:10px;line-height:12px;color:var(--ink)}
  .cover-title{position:absolute;left:0;right:0;top:136px;font-family:"Lexend",sans-serif}
  .cover-title .line1{display:block;font-size:29px;line-height:31px;font-weight:400;color:var(--ink);letter-spacing:-.5px}
  .cover-for{display:flex;align-items:center;justify-content:center;gap:8px;margin:6px 0 2px;font-size:14px;letter-spacing:5px;color:var(--ink)}
  .cover-for::before,.cover-for::after{content:"";width:44px;height:1px;background:var(--rule)}
  .cover-title .line2{display:block;font-size:35px;line-height:37px;font-weight:600;color:var(--green);letter-spacing:-.8px}
  .cover-art{position:absolute;left:0;right:0;bottom:0;height:250px;background:linear-gradient(180deg,rgba(242,233,224,0) 0%,#e6d8bd 30%,#d8c59f 70%,#cdb98f 100%)}

  /* Inner sheet */
  .panel--context{background:var(--white);padding:18px 12px 0 16px}
  .panel--community{background:var(--sage);padding:16px 12px 0 13px}
  .panel--capacity{background:linear-gradient(90deg,#f3f3f3,var(--white) 40%);padding:16px 12px 0 16px}
  .section-title{font-size:14.5px;line-height:15px;font-weight:500;margin-bottom:5px;letter-spacing:-.2px}
  .section-lead{font-size:9px;line-height:11.8px;font-weight:400;color:#2c2c2c;margin-bottom:5px}
  .ticks{list-style:none}
  .ticks li{position:relative;padding-left:12px;font-size:8.6px;line-height:11.7px;letter-spacing:-.15px;margin-bottom:4.6px}
  .ticks li::before{content:"";position:absolute;left:2px;top:2px;width:3px;height:6px;border:solid var(--green);border-width:0 1.5px 1.5px 0;transform:rotate(40deg)}
  .gap{height:14px}
</style>
</head>
<body>

<section class="sheet sheet--outer" aria-label="Brochure outer side">
  <div class="panel panel--intro">
    <h2 class="intro-title">Harbourline Charter for<br>Community Mending</h2>
    <p>Disasters can deeply impact lives and livelihoods. Working with communities recovering from disasters is complex and challenging. Recovery is long-term, non-linear and dynamic, particularly in the context of compounding and concurrent disasters. These principles are a way to guide our efforts, our approach, our planning and our decision-making.</p>
    <p>Disaster recovery is part of emergency management, which includes the broader components of prevention, preparedness &amp; response. Planning for recovery is integral to emergency preparation, and mitigation actions are often initiated as part of recovery.</p>
    <p>Disaster recovery includes built, environmental and economic elements, as well as individual and social wellbeing. Recovery can provide an opportunity to improve these aspects beyond previous conditions, by enhancing social and natural environments, infrastructure and economies – contributing to more resilient communities.</p>
    <div class="relationship">
      <h4>The relationship between the principles</h4>
      <p>While all the principles are equally critical to ensure effective recovery, understanding the local and broader context and recognising complexity are foundational. The descriptions beneath each principle provide further guidance for working with communities in disaster recovery.</p>
    </div>
    <h3 class="success-label">SUCCESSFUL RECOVERY</h3>
    <h4 class="principle-sm">Understand the <span class="accent">Context</span></h4>
    <p>Successful recovery is based on an understanding of the community context, with each community having its own history, values and dynamics.</p>
  </div>

  <div class="panel panel--overview">
    <h4 class="principle-sm">Recognise <span class="accent">Complexity</span></h4>
    <p>Successful recovery is responsive to the complex and evolving nature of disasters and their impacts on communities, including compounding, cascading and concurrent events.</p>
    <h4 class="principle-sm">Use <span class="accent">Community Centered</span> approaches</h4>
    <p>Successful recovery is community-centred, responsive and flexible, engaging with community and supporting them to move forward, with shared responsibilities.</p>
    <h4 class="principle-sm"><span class="accent">Coordinate</span> all activities</h4>
    <p>Successful recovery requires a planned, coordinated and adaptive approach, between community and partner agencies, based on continuing assessment of impacts and needs.</p>
    <h4 class="principle-sm"><span class="accent">Communicate</span> effectively</h4>
    <p>Successful recovery is built on effective communication between the affected community and other partners.</p>
    <h4 class="principle-sm">Recognise &amp; build <span class="accent">Capacity</span></h4>
    <p>Successful recovery recognises, supports and builds on individual, community and organisational capacity and resilience.</p>

    <div class="partner-box" aria-label="Partner organisations">
      <svg width="205" height="183" viewBox="0 0 205 189" preserveAspectRatio="none" aria-hidden="true">
        <g fill="var(--logo-grey)">
          <circle cx="58" cy="20" r="9"/><rect x="30" y="33" width="56" height="4" rx="2"/><rect x="34" y="41" width="48" height="3" rx="1.5"/>
          <circle cx="146" cy="20" r="9"/><rect x="118" y="33" width="56" height="4" rx="2"/><rect x="122" y="41" width="48" height="3" rx="1.5"/><rect x="122" y="47" width="48" height="3" rx="1.5"/>
          <circle cx="40" cy="80" r="13"/><circle cx="82" cy="78" r="11"/><circle cx="124" cy="78" r="11"/><rect x="152" y="68" width="30" height="22" rx="3"/>
          <circle cx="40" cy="123" r="11"/><rect x="70" y="110" width="24" height="30" rx="3"/><rect x="124" y="112" width="44" height="26" rx="3"/>
          <circle cx="40" cy="166" r="10"/><rect x="56" y="160" width="40" height="12" rx="2"/><rect x="108" y="156" width="18" height="20" rx="3"/><rect x="132" y="160" width="52" height="12" rx="2"/>
        </g>
      </svg>
    </div>
  </div>

  <div class="panel panel--cover">
    <div class="brand">
      <span class="brand-mark" aria-hidden="true"></span>
      <span class="brand-name">Kinship Recovery<br>Circle Australia</span>
    </div>
    <h1 class="cover-title">
      <span class="line1">Harbourline<br>Charter</span>
      <span class="cover-for">FOR</span>
      <span class="line2">Community<br>Mending</span>
    </h1>
    <div class="cover-art" role="img" aria-label="Soft sepia illustration of a river valley with mountains, trees, wildflowers and birds in flight"></div>
  </div>
</section>

<section class="sheet sheet--inner" aria-label="Brochure inner side">
  <div class="panel panel--context">
    <h3 class="section-title">Understand the <span class="accent">Context</span></h3>
    <p class="section-lead">Successful recovery is based on an understanding of the community context, with each community having its own history, values and dynamics.</p>
    <ul class="ticks">
      <li>Acknowledge existing strengths and capacity, including past experiences and future aspirations.</li>
      <li>Appreciate the risks &amp; stressors faced by community.</li>
      <li>Embed accessibility, equity, inclusion and diversity in recovery practice, using culturally safe and trauma-informed approaches.</li>
      <li>Support people who may be at greater risk or disproportionately impacted.</li>
      <li>Respect and support connections to Country, environment, animals and culturally significant places &amp; recognise environmental regeneration in recovery.</li>
      <li>Recognise pathways and timeframes vary; systems should support long-term recovery shaped by community needs.</li>
      <li>Acknowledge the impact upon the community may extend beyond the geographical boundaries where the disaster occurred.</li>
    </ul>
    <div class="gap"></div>
    <h3 class="section-title">Recognise <span class="accent">Complexity</span></h3>
    <p class="section-lead">Successful recovery is responsive to the complex and evolving nature of disasters and their impacts on communities.</p>
    <ul class="ticks">
      <li>Disasters lead to a range of effects and impacts that require a variety of approaches; they can also leave long-term legacies.</li>
      <li>Information on impacts and needs can be limited at first and changes over time.</li>
      <li>Affected individuals and the community have diverse needs, wants &amp; expectations.</li>
      <li>Responsive and flexible action is crucial to addressing immediate needs.</li>
    </ul>
  </div>

  <div class="panel panel--community">
    <ul class="ticks">
      <li>Existing community values may challenge the assumptions of those outside of the community.</li>
      <li>Conflicting knowledge, values and priorities, the community and organisations may create tensions.</li>
      <li>Emergencies create stressful environments where grief or blame may also affect those involved.</li>
      <li>Support for individuals and communities, from within &amp; outside, can cultivate hope &amp; collective growth.</li>
    </ul>
    <div class="gap"></div>
    <h3 class="section-title">Use <span class="accent">Community-Centred</span><br>Approaches</h3>
    <p class="section-lead">Successful recovery is community-centred, responsive and flexible, engaging with community and supporting them to move forward, with shared responsibilities.</p>
    <ul class="ticks">
      <li>Assist &amp; enable individuals, families &amp; the community to actively participate in their own recovery.</li>
      <li>Recognise that individuals and the community may need different levels of support at various times.</li>
      <li>Effort through pre-identified and existing community assets, local knowledge, strengths and resilience.</li>
      <li>Build collaborative partnerships that reflect diverse representation and community leadership in recovery.</li>
      <li>Support Aboriginal and Torres Strait Islander self-determination and Indigenous governance, recognising Country as central to recovery &amp; resilience.</li>
      <li>Recognise that new community leaders often emerge during and after a disaster.</li>
      <li>Recognise that different communities may choose different paths to recovery.</li>
    </ul>
    <div class="gap"></div>
    <h3 class="section-title"><span class="accent">Communicate</span> Effectively</h3>
    <p class="section-lead">Successful recovery is built on effective communication between the affected community and other partners.</p>
  </div>

  <div class="panel panel--capacity">
    <ul class="ticks">
      <li>Recognise that communication should be two-way, transparent and ongoing, building trust through shared understanding and feedback.</li>
      <li>Ensure that information is accessible to audiences in diverse situations, addresses communication needs, and is provided through a range of communication channels and networks.</li>
      <li>Establish mechanisms for coordinated and consistent communications between all service providers.</li>
      <li>Ensure that all communication is relevant, timely, clear, accurate, targeted, credible and consistent.</li>
      <li>Identify trusted sources of information and repeat key recovery messages to enable greater community confidence and receptivity.</li>
    </ul>
    <div class="gap" style="height:6px"></div>
    <h3 class="section-title">Recognise &amp; build <span class="accent">Capacity</span></h3>
    <p class="section-lead">Successful recovery recognises, supports and builds on individual, community &amp; organisational capacity and resilience.</p>
    <ul class="ticks">
      <li>Assess capability and capacity requirements before, during and after a disaster. Support the development of self-reliance, preparation and disaster mitigation.</li>
      <li>Quickly identify and mobilise community skills, strengths and resources. Develop networks and partnerships to strengthen capacity, capability and resilience. Support training and knowledge sharing to sustain recovery capability. Mental health &amp; wellbeing supports are for all involved in disaster recovery.</li>
      <li>Recognise that resources can be provided by a range of partners and from community networks.</li>
      <li>Acknowledge that existing resources may be stretched, and additional resources may required.</li>
      <li>Additional resources only be available for a limited period, and sustainability may need to be addressed.</li>
      <li>When &amp; to step back, while continuing to support individuals &amp; community to be more self-sufficient. Monitor, evaluate and capture learning to strengthen future recovery.</li>
    </ul>
  </div>
</section>

</body>
</html>
```